Business Card for Coastal Tundrabridge Advisory

We need a business card for Coastal Tundrabridge Advisory. The company website address is provided below. The company logo is attached. We provide specialized permafrost services to the mining, transportation, and oil & gas industries. The card should be prepared for:
Matthias Korhonen, PhD.
Coastal Tundrabridge Advisory
PO Box 418259
Quillwater, Alaska 99642
Direct: +1-907-555-0143
Email: mkorhonen@tundrabridgeadvisory.example
Website: www.coastaltundrabridgeadvisory.example

```html
<!DOCTYPE html>
<html lang="en">
<head>
<meta charset="utf-8">
<title>Coastal Tundrabridge Advisory – Business Card</title>
<link href="https://fonts.googleapis.com/css2?family=Montserrat:wght@400;600;700&display=swap" rel="stylesheet">
<style>
  :root {
    --backdrop: #d8d3cb;
    --card-light: #ffffff;
    --card-dark: #2a2a2a;
    --ink: #1d232b;
    --band-dark: #333235;
    --band-grey: #6b6b6b;
    --on-dark: #ffffff;
    --mark-light: #c9c9c9;
  }
  * { margin: 0; padding: 0; box-sizing: border-box; }
  html, body {
    width: 900px; height: 1200px; overflow: hidden;
    background: var(--backdrop);
    font-family: "Montserrat", sans-serif;
  }
  .card {
    position: absolute; left: 80px; width: 742px; height: 440px;
    border-radius: 38px; overflow: hidden;
  }
  .card--front { top: 132px; background: var(--card-light); color: var(--ink); }
  .card--back { top: 640px; background: var(--card-dark); }

  .brand-name {
    position: absolute; font-weight: 700; text-transform: uppercase;
    letter-spacing: 2px; line-height: 1.1;
  }
  .card--front .brand-name { left: 56px; top: 50px; font-size: 30px; color: var(--ink); }
  .card--back .brand-name {
    left: 0; right: 0; top: 172px; text-align: center;
    font-size: 36px; color: var(--mark-light);
  }

  .holder { position: absolute; left: 30px; top: 180px; }
  .holder__name { font-size: 25px; font-weight: 700; }
  .holder__title { font-size: 15.5px; font-weight: 400; margin-top: 2px; margin-left: 1px; }

  .contact-band { position: absolute; left: 0; top: 255px; width: 742px; height: 103px; }
  .contact-list {
    position: absolute; left: 45px; top: 275px; list-style: none;
    color: var(--on-dark); font-size: 15.5px; line-height: 22.5px;
  }
  .contact-list li { display: flex; align-items: center; gap: 10px; }
  .contact-list svg { width: 14px; height: 14px; fill: var(--on-dark); flex: none; }

  .address { position: absolute; left: 42px; top: 374px; font-size: 15.5px; line-height: 21px; }
</style>
</head>
<body>
  <section class="card card--front">
    <div class="brand-name">Coastal Tundrabridge<br>Advisory</div>

    <div class="holder">
      <div class="holder__name">Matthias Korhonen, PhD.</div>
      <div class="holder__title">CEO &amp; Founder</div>
    </div>

    <svg class="contact-band" viewBox="0 0 742 103" aria-hidden="true">
      <polygon points="0,0 520,0 458,103 0,103" fill="var(--band-dark)"/>
      <polygon points="530,0 742,0 742,103 468,103" fill="#ffffff"/>
      <polygon points="538,0 742,0 742,103 476,103" fill="var(--band-grey)"/>
    </svg>

    <ul class="contact-list">
      <li><svg viewBox="0 0 16 16"><path d="M1 6c0-2 3-4 7-4s7 2 7 4v1h-4V5H5v2H1z M3 8h10l1 6H2z"/></svg>+1-907-555-0143</li>
      <li><svg viewBox="0 0 16 16"><path d="M1 3h14v2L8 9 1 5z M1 7l7 4 7-4v6H1z"/></svg>mkorhonen@tundrabridgeadvisory.example</li>
      <li><svg viewBox="0 0 16 16"><circle cx="8" cy="8" r="7"/></svg>www.coastaltundrabridgeadvisory.example</li>
    </ul>

    <address class="address" style="font-style:normal">
      PO Box 418259<br>
      Quillwater, Alaska 99642
    </address>
  </section>

  <section class="card card--back">
    <div class="brand-name">Coastal Tundrabridge<br>Advisory</div>
  </section>
</body>
</html>
```